Every Shelf Set Neatly or ESN Organized needs a business card design. ESN Organized is a professi

We need a business card design that is clean, sharp and conveys a sense of organization. I already have a logo.

Target Market(s)

Families (specifically mothers), small business owners, parents, seniors

Industry/Entity Type

Business

Contact Information for Business Card

My website is www.esnorganized-example.com and my Facebook page is http://www.sociallink-example.com/everyshelfsetneatly. The phone number is 418-552-7094 and I want to be listed as Lorna M. Pelham, Owner

Requirements
Must have
• My logo.

```html
<!DOCTYPE html>
<html lang="en">
<head>
<meta charset="utf-8">
<title>ESN Organized — Business Card</title>
<link rel="stylesheet" href="https://fonts.googleapis.com/css2?family=Montserrat:wght@400;500&display=swap">
<style>
  :root {
    --stage: #2b2b2c;
    --card-dark: #050607;
    --card-light: #f1f1f0;
    --brand-blue: #1b7fd6;
    --text-light: #e6e8ea;
    --text-dark: #1a1a1a;
  }
  * { margin: 0; padding: 0; box-sizing: border-box; }
  html, body {
    width: 1200px; height: 840px; overflow: hidden;
    background: var(--stage);
    font-family: "Montserrat", Arial, sans-serif;
  }
  .stage { position: relative; width: 1200px; height: 840px; }

  .card {
    position: absolute;
    width: 459px; height: 262px;
    box-shadow: 0 10px 18px rgba(0,0,0,0.45);
  }

  /* Back of card: contact details */
  .card-back { left: 452px; top: 121px; background: var(--card-dark); }
  .divider-line {
    position: absolute; left: 76px; top: 80px;
    width: 2px; height: 138px; background: var(--brand-blue);
  }
  .icon {
    position: absolute; left: 46px; width: 14px; height: 14px;
    fill: var(--brand-blue);
  }
  .icon-person { top: 124px; width: 16px; height: 16px; left: 45px; }
  .icon-phone { top: 160px; }
  .icon-web { top: 180px; }
  .icon-social { top: 199px; }
  .contact-name {
    position: absolute; left: 101px; top: 107px;
    font-size: 18px; font-weight: 400; letter-spacing: 0.4px;
    color: var(--brand-blue);
  }
  .contact-role {
    position: absolute; left: 101px; top: 131px;
    font-size: 13px; color: var(--text-light); letter-spacing: 0.4px;
  }
  .contact-line {
    position: absolute; left: 101px;
    font-size: 12.5px; color: var(--text-light); letter-spacing: 0.3px;
  }
  .line-phone { top: 160px; }
  .line-web { top: 179px; }
  .line-social { top: 198px; }

  /* Front of card: brand name */
  .card-front { left: 318px; top: 442px; background: var(--card-light); }
  .brand-name {
    position: absolute; left: 0; right: 0; top: 118px;
    text-align: center;
    font-size: 24px; font-weight: 500; letter-spacing: 3px;
    color: var(--brand-blue);
  }
</style>
</head>
<body>
<main class="stage">

  <section class="card card-back" aria-label="Business card back">
    <div class="divider-line"></div>

    <svg class="icon icon-person" viewBox="0 0 16 16" aria-hidden="true">
      <circle cx="8" cy="5" r="3.6"/>
      <path d="M1 16c0-4 3-6.5 7-6.5s7 2.5 7 6.5z"/>
    </svg>
    <p class="contact-name">Lorna M. Pelham</p>
    <p class="contact-role">Owner</p>

    <svg class="icon icon-phone" viewBox="0 0 16 16" aria-hidden="true">
      <path d="M3.5 1l2.6 3.2-1.5 1.8c.9 2 2.5 3.6 4.5 4.5l1.8-1.5L14 11.6 12.3 14C6.5 13.6 2.4 9.5 2 3.7z"/>
    </svg>
    <p class="contact-line line-phone">418-552-7094</p>

    <svg class="icon icon-web" viewBox="0 0 16 16" aria-hidden="true">
      <circle cx="8" cy="8" r="6.5" fill="none" stroke="var(--brand-blue)" stroke-width="1.6"/>
      <path d="M1.5 8h13M8 1.5c-3 3.5-3 9.5 0 13M8 1.5c3 3.5 3 9.5 0 13" fill="none" stroke="var(--brand-blue)" stroke-width="1.2"/>
    </svg>
    <p class="contact-line line-web">www.esnorganized-example.com</p>

    <svg class="icon icon-social" viewBox="0 0 16 16" aria-hidden="true">
      <rect x="1.5" y="1.5" width="13" height="13"/>
    </svg>
    <p class="contact-line line-social">/everyshelfsetneatly</p>
  </section>

  <section class="card card-front" aria-label="Business card front">
    <p class="brand-name">ESN ORGANIZED</p>
  </section>

</main>
</body>
</html>
```